Alternative Country Rock Band Needs Website Design

Cal Brimley and The Dustriders Web Design Proposal

Overview
We essentially need design and code for an uncluttered, easy to navigate, simple to access repository for our music, videos, photos, up and coming shows, merchandise, and links to social media. It will be a platform for our fans, new and old to get to the heart of who we are and what we are doing. We want something that will embody our essence as musicians, our distinct flavor, and values. We must be able to add, remove and edit content without developer help.

*If we receive a design so good that it justifies no code, we are open to that*

Chatterbox
It would be nice to have Chatterbox integration so that much of the site can be liked, possibly commented on but most importantly shared.

This could also possibly be done on Skimlog http://www.skimlog-example.com/ which posts right to Peeplet feeds and Chatterbox with cross links back.

Smart Phone
We need the site to be compatible with smart phones.

Branding/Aesthetics

We are really keen on aesthetics. We are almost more concerned about the feel of the site than content, which of course will be there.

We want to aim at an edgy, gritty, folky rock ‘n’ roll with a cowboy kick ambiance. We want the space to have a Southwestern romanticism risqué tinge. We want something that feels similar to our new EP album cover “Dust On Silver.”

Our image is huge and we want people, agents, managers, venues, friends, family, and fans to see who we are immediately and be able to easily connect to us, share us, and contact us.

Content

Our GigHarbor and Chatterbox already exists, so much of it can essentially be reworked into the new site.

We want an About; Shows; Music; Videos (maybe combine as just “Music” so that we don’t clutter the site); Photos; Media/Press (one of the two); Store; Contact Us (booking inquiries etc.) and Easy Big Connectors to Social Media; Email List (somewhere, probably not in navigation)

Examples

These are band sites that we think more or less hit the nail on the head. When reviewing them, it seems we are drawn to sites that have very large pictures, large, easy to use navigation buttons and such.

http://marlowfenwick-example.com/

http://www.velvetorchardband-example.com/

http://theironheron-example.com/

http://www.gandersonmusic-example.com/site/

http://www.thequietlarks-example.com/ (love the size of the photos but don’t like the small navigation)

Hosting
Ploomby has been recommended and it is free, but let us know if you know a better one.

Content Management
We want to be able to upload our shows using GigHarbor and that they will show on our website, likely by using an RSS Feed. It might even be nice if music, photos and videos could also be linked. Basic Ruby on Rails has been recommended for content management, making it easier to add and remove content, but maybe you know better.

However, we are open to Neat Panel or Zub as a prefabricated content management system as well.

Latest Technologies
We need the site up to date with the latest technologies out there, rss feeds, and so on so it will show up on search engines.
Updates

Project Deadline Extended
Reason: A number of designers accepted the job and are yet to submit their work.

Project Deadline Extended
Reason: We are looking for some original design elements. It seems many have over utilized our pictures to supplement design. We've added another $200 on top of the original $300 for a total of $500 for the project. We look forward to your participation!

We've added $200 to bring the total to $500 for our web design.  We are looking forward to your ideas...

Hi Designers,

We've added some more band pictures and posters for inspiration for possible designs.  We look forward to your submissions!

Cal Brimley

Industry/Entity Type

Store

Font styles to use
Sans Serif
Decorative

```html
<!DOCTYPE html>
<html lang="en">
<head>
<meta charset="utf-8">
<title>Cal Brimley and The Dustriders</title>
<link rel="stylesheet" href="https://fonts.googleapis.com/css2?family=Rye&family=Cabin:wght@400;700&family=PT+Sans:wght@400;700&display=swap">
<style>
  :root {
    --page-bg: #1e1e1e;
    --panel-bg: #262626;
    --footer-bg: #2b2b2b;
    --rule: #5a5a5a;
    --text: #e6e6e6;
    --muted: #bdbdbd;
    --link-blue: #9fb8e8;
    --tile-blue: #2e64b4;
    --tile-orange: #e89a1f;
    --tile-sky: #3aa8e0;
    --tile-red: #e1453c;
    --progress: #cc1a1a;
  }
  * { box-sizing: border-box; margin: 0; padding: 0; }
  html, body { width: 798px; height: 1200px; overflow: hidden; }
  body {
    position: relative;
    background:
      repeating-linear-gradient(45deg, rgba(255,255,255,.018) 0 1px, transparent 1px 3px),
      repeating-linear-gradient(-45deg, rgba(0,0,0,.12) 0 1px, transparent 1px 3px),
      var(--page-bg);
    color: var(--text);
    font-family: "PT Sans", sans-serif;
  }
  .hero-photo {
    position: absolute; left: 0; top: 0; width: 798px; height: 362px;
    background:
      radial-gradient(ellipse 60% 45% at 75% 8%, rgba(235,235,235,.85), transparent 70%),
      radial-gradient(ellipse 40% 35% at 10% 5%, rgba(200,200,200,.6), transparent 70%),
      linear-gradient(180deg, rgba(0,0,0,0) 0%, rgba(10,10,10,.55) 30%, rgba(20,20,20,.5) 55%, rgba(110,110,110,.35) 72%, rgba(30,30,30,.9) 90%, var(--page-bg) 100%),
      linear-gradient(90deg, #6a6a6a, #9a9a9a 40%, #7a7a7a 70%, #b0b0b0);
  }
  .main-nav {
    position: absolute; left: 13px; top: 384px; width: 760px;
    display: flex; justify-content: space-between;
    font-family: "Rye", serif; font-size: 15px; color: #f4f4f4;
    text-shadow: 0 0 1px #000;
  }
  .main-nav a { color: inherit; text-decoration: none; }
  .page-title {
    position: absolute; left: 20px; top: 436px;
    font-family: "Rye", serif; font-size: 23px; font-weight: normal; color: #f2f2f2;
  }
  .video { position: absolute; left: 20px; top: 479px; width: 573px; height: 341px; }
  .video-frame {
    height: 321px;
    background: linear-gradient(120deg, #6a3a52 0%, #b85a6a 30%, #5a3b78 60%, #2a1f3a 100%);
  }
  .video-controls {
    position: relative; height: 20px; background: #1b1b1b;
    border-top: 3px solid #444;
  }
  .video-controls .progress { position: absolute; left: 0; top: -3px; width: 420px; height: 3px; background: var(--progress); }
  .video-controls .buffer { position: absolute; left: 420px; top: -3px; width: 25px; height: 3px; background: #888; }
  .video-controls .time { position: absolute; left: 60px; top: 2px; font-size: 10px; color: #ddd; }
  .video-controls svg { position: absolute; top: 4px; }
  .body-copy {
    position: absolute; left: 12px; top: 829px; width: 586px;
    font-size: 9.9px; line-height: 16.2px; color: var(--text);
  }
  .sidebar-heading {
    position: absolute; left: 613px; width: 182px; height: 36px;
    background: var(--panel-bg);
    font-family: "Cabin", sans-serif; font-size: 21px; font-weight: normal;
    padding: 4px 0 0 8px; color: #f5f5f5;
  }
  .tile {
    position: absolute; display: flex; align-items: center; justify-content: center;
    font-family: "PT Sans", sans-serif; font-weight: 700; color: #fff;
  }
  .tile-chatterbox { left: 619px; top: 477px; width: 80px; height: 93px; background: var(--tile-blue); font-size: 13px; }
  .tile-feed { left: 701px; top: 477px; width: 80px; height: 45px; background: var(--tile-orange); font-size: 13px; }
  .tile-peeplet { left: 701px; top: 525px; width: 80px; height: 45px; background: var(--tile-sky); font-size: 13px; }
  .tile-clipcast { left: 619px; top: 573px; width: 162px; height: 46px; background: var(--tile-red); font-size: 14px; }
  .signup-label { position: absolute; left: 618px; top: 627px; font-size: 10px; color: var(--muted); }
  .signup-input { position: absolute; left: 618px; top: 652px; width: 175px; height: 25px; background: #f4f4f4; border: 1px solid #999; }
  .signup-button {
    position: absolute; left: 618px; top: 687px; width: 61px; height: 20px;
    background: #2c2c2c; border: 1px solid #555; color: #ddd; font-size: 10px;
    font-family: "PT Sans", sans-serif; text-align: center; line-height: 18px;
  }
  .fan-box { position: absolute; left: 618px; top: 768px; width: 168px; height: 352px; }
  .fan-box-header {
    height: 17px; background: #333; font-size: 8px; font-weight: 700; padding: 3px 4px; color: #fff;
  }
  .fan-page { display: flex; gap: 6px; padding: 7px 6px 6px; border-bottom: 1px solid #666; }
  .fan-page-avatar { width: 32px; height: 32px; background: linear-gradient(#8a7a66, #3c342c); }
  .fan-page-name { font-size: 8.6px; font-weight: 700; color: #fff; }
  .like-button {
    display: inline-block; margin-top: 3px; padding: 1px 4px; font-size: 8px;
    background: #4a66a8; color: #fff; border: 1px solid #6f86bd;
  }
  .fan-count { font-size: 7.5px; color: #aaa; padding: 4px 4px 5px; }
  .fan-count b { color: var(--link-blue); }
  .fan-grid {
    display: grid; grid-template-columns: repeat(4, 32px); gap: 3px 3px;
    padding-left: 7px; width: 160px;
  }
  .fan-grid span { width: 32px; height: 32px; display: block; }
  .fan-box-footer { margin-top: 8px; border-top: 1px solid #666; font-size: 7.5px; color: #ddd; padding: 3px 6px; }
  .site-footer {
    position: absolute; left: 0; top: 1145px; width: 798px; height: 55px;
    background: var(--footer-bg); border-top: 2px solid var(--rule);
    text-align: center; font-size: 10px; color: #eee; line-height: 16px; padding-top: 12px;
  }
  .site-footer a { color: inherit; text-decoration: none; }
</style>
</head>
<body>
  <div class="hero-photo" role="img" aria-label="Black and white band photo: six musicians in cowboy hats and boots leaning on a wooden fence in a rocky hillside"></div>

  <nav class="main-nav">
    <a href="#">Home</a><a href="#">About</a><a href="#">Shows</a><a href="#">Music</a><a href="#">Videos</a><a href="#">Photos</a><a href="#">Media/Press</a><a href="#">Store</a><a href="#">Contact Us</a>
  </nav>

  <h1 class="page-title">Live at NameClub</h1>

  <div class="video">
    <div class="video-frame" role="img" aria-label="Live video still: singer with acoustic guitar at a microphone under pink and purple stage lights"></div>
    <div class="video-controls">
      <div class="progress"></div><div class="buffer"></div>
      <svg style="left:14px" width="10" height="11" viewBox="0 0 10 11"><path d="M0 0 L9 5.5 L0 11Z" fill="#ccc"/></svg>
      <svg style="left:38px" width="10" height="11" viewBox="0 0 10 11"><path d="M0 3.5 H3 L7 0 V11 L3 7.5 H0Z" fill="#ccc"/></svg>
      <span class="time">8:51 / 11:58</span>
      <svg style="left:540px" width="10" height="10" viewBox="0 0 10 10"><rect x="0.5" y="0.5" width="9" height="8" fill="none" stroke="#ccc"/></svg>
      <svg style="left:558px" width="10" height="10" viewBox="0 0 10 10"><path d="M0 3V0H3M7 0H10V3M10 7V10H7M3 10H0V7" fill="none" stroke="#ccc" stroke-width="1.5"/></svg>
    </div>
  </div>

  <p class="body-copy">Lorem ipsum dolor sit amet, consectetuer adipiscing elit, sed diam nonummy nibh euismod tincidunt ut laoreet dolore magna aliquam erat volutpat. Ut wisi enim ad minim veniam, quis nostrud exerci tation ullamcorper suscipit lobortis nisl ut aliquip ex ea commodo consequat. Duis autem vel eum iriure dolor in hendrerit in vulputate velit esse molestie consequat, vel illum dolore eu feugiat nulla facilisis at vero eros et accumsan et iusto odio dignissim qui blandit praesent luptatum zzril delenit augue duis dolore te feugait nulla facilisi. Nam liber tempor cum soluta nobis eleifend option congue nihil imperdiet doming id quod mazim placerat facer possim assum. Typi non habent claritatem insitam; est usus legentis in iis qui facit eorum claritatem. Investigationes demonstraverunt lectores legere me lius quod ii legunt saepius. Claritas est etiam processus dynamicus, qui sequitur mutationem consuetudium lectorum. Mirum est notare quam littera gothica, quam nunc putamus parum claram, anteposuerit litterarum formas humanitatis per seacula quarta decima et quinta decima. Eodem modo typi, qui nunc nobis videntur parum clari, fiant sollemnes in futurum.</p>

  <h2 class="sidebar-heading" style="top:425px">Folow Us</h2>
  <a class="tile tile-chatterbox">Chatterbox</a>
  <a class="tile tile-feed">Feed</a>
  <a class="tile tile-peeplet">Peeplet</a>
  <a class="tile tile-clipcast">Clipcast</a>

  <label class="signup-label">Your e-mail address</label>
  <div class="signup-input"></div>
  <div class="signup-button">Subscribe</div>

  <h2 class="sidebar-heading" style="top:724px">Our Fans</h2>
  <div class="fan-box">
    <div class="fan-box-header">Find us on Chatterbox</div>
    <div class="fan-page">
      <div class="fan-page-avatar" role="img" aria-label="Band page avatar"></div>
      <div>
        <div class="fan-page-name">Cal Brimley and The Dustriders</div>
        <span class="like-button">Like</span>
      </div>
    </div>
    <div class="fan-count">2,145 people like <b>Cal Brimley and The Dustriders</b></div>
    <div class="fan-grid" role="img" aria-label="Grid of fan profile pictures">
      <span style="background:#a89a7a"></span><span style="background:#5a4a40"></span><span style="background:#6a6a6a"></span><span style="background:#8a6a5a"></span>
      <span style="background:#7a3a3a"></span><span style="background:#9a8a70"></span><span style="background:#c8b890"></span><span style="background:#6a5a4a"></span>
      <span style="background:#5a7a4a"></span><span style="background:#4a4a5a"></span><span style="background:#2a2a3a"></span><span style="background:#c8a040"></span>
      <span style="background:#8a9ab0"></span><span style="background:#7a8ab8"></span><span style="background:#a0a0a0"></span><span style="background:#3a3030"></span>
      <span style="background:#6a5040"></span><span style="background:#a08a7a"></span><span style="background:#7a6a5a"></span><span style="background:#5a3a30"></span>
      <span style="background:#b09080"></span><span style="background:#3a3a3a"></span><span style="background:#8a9aa0"></span><span style="background:#9a9a9a"></span>
      <span style="background:#4a3a3a"></span><span style="background:#8a5a7a"></span><span style="background:#c0a890"></span><span style="background:#5a4a4a"></span>
    </div>
    <div class="fan-box-footer">Chatterbox social plugin</div>
  </div>

  <footer class="site-footer">
    <div><a href="#">Home</a> | <a href="#">About</a> | <a href="#">Shows</a> | <a href="#">Music</a> | <a href="#">Videos</a> | <a href="#">Photos</a> | <a href="#">Media/Press</a> | <a href="#">Store</a> | <a href="#">Contact Us</a></div>
    <div>Copyright © 2011-2012. All Rights Reserved.</div>
  </footer>
</body>
</html>
```